Harbor Ledger Funds Bus card and Logo

I need a logo design and Bus card design. The fund focuses on evaluating and investing in minerals (sub-surface rights) and real estate.

Harbor ledger refers to a book of knowledge that each plebe gets when entering the Kelmont Marine Academy (my alma mater)

Target Market(s)

Investors and financial advisors

Contact Information for Business Card

Simple - perhaps a logo with a theme on book of knowledge

Logo Text

Ex Scientia Imperium

Font styles to use
Serif
Sans Serif

Colors

Designer to choose colors to be used in the design.

Requirements
Must have
• memorable logo that is relatively simple

```html
<!DOCTYPE html>
<html lang="en">
<head>
<meta charset="utf-8">
<title>Harbor Ledger Funds – Business Card</title>
<link rel="stylesheet" href="https://fonts.googleapis.com/css2?family=Open+Sans:wght@400;600;700&display=swap">
<style>
  :root {
    --backdrop: #2a2a2c;
    --card: #19191a;
    --card-edge: #111112;
    --accent-green: #7cc63a;
    --accent-blue: #3a9ad8;
    --text-light: #e4e4e4;
    --text-muted: #a9a9ab;
    --divider: #4a4a4c;
  }
  html, body {
    margin: 0;
    padding: 0;
    width: 1200px;
    height: 900px;
    overflow: hidden;
    background: var(--backdrop);
    font-family: "Open Sans", Arial, sans-serif;
  }
  .canvas {
    position: relative;
    width: 1200px;
    height: 900px;
    background: radial-gradient(ellipse at 50% 40%, #323234 0%, var(--backdrop) 70%);
  }
  .card {
    position: absolute;
    left: 320px;
    width: 560px;
    height: 320px;
    background: linear-gradient(160deg, #1f1f20 0%, var(--card) 60%, var(--card-edge) 100%);
    box-shadow: 0 14px 30px rgba(0,0,0,0.45);
    overflow: hidden;
  }
  .card::after {
    content: "";
    position: absolute;
    left: 0; right: 0; bottom: 0;
    height: 9px;
    background: var(--accent-green);
  }
  .card--front { top: 100px; }
  .card--back  { top: 470px; }

  /* Front */
  .brand {
    position: absolute;
    left: 0; right: 0;
    top: 70px;
    display: flex;
    flex-direction: column;
    align-items: center;
  }
  .brand__dot {
    width: 64px;
    height: 64px;
    border-radius: 50%;
    background: var(--accent-blue);
    margin-bottom: 16px;
  }
  .brand__name {
    color: var(--text-light);
    font-weight: 600;
    font-size: 34px;
    letter-spacing: 0.5px;
    line-height: 1;
  }
  .brand__sub {
    color: var(--text-light);
    font-weight: 600;
    font-size: 13px;
    letter-spacing: 9px;
    margin-top: 8px;
    padding-left: 9px;
  }

  /* Back */
  .holder {
    position: absolute;
    left: 130px;
    top: 92px;
    text-align: left;
  }
  .holder__name {
    color: var(--accent-green);
    font-weight: 700;
    font-size: 19px;
    letter-spacing: 0.5px;
    margin: 0;
  }
  .holder__title {
    color: var(--text-muted);
    font-size: 14px;
    margin: 2px 0 0;
  }
  .divider {
    position: absolute;
    left: 300px;
    top: 84px;
    width: 1px;
    height: 86px;
    background: var(--divider);
  }
  .contact {
    position: absolute;
    left: 318px;
    top: 86px;
    list-style: none;
    margin: 0;
    padding: 0;
  }
  .contact__item {
    display: flex;
    align-items: center;
    gap: 9px;
    color: var(--text-light);
    font-size: 15px;
    line-height: 21px;
  }
  .contact__icon {
    width: 12px;
    height: 12px;
    flex: none;
    fill: var(--accent-green);
  }
  .address {
    position: absolute;
    left: 70px;
    top: 210px;
    color: var(--text-muted);
    font-size: 15px;
    margin: 0;
  }
</style>
</head>
<body>
<main class="canvas">

  <section class="card card--front" aria-label="Business card front">
    <div class="brand">
      <div class="brand__dot"></div>
      <div class="brand__name">HARBOR LEDGER</div>
      <div class="brand__sub">FUNDS</div>
    </div>
  </section>

  <section class="card card--back" aria-label="Business card back">
    <div class="holder">
      <h1 class="holder__name">EVAN MARSH</h1>
      <p class="holder__title">Managing Director</p>
    </div>
    <div class="divider"></div>
    <ul class="contact">
      <li class="contact__item">
        <svg class="contact__icon" viewBox="0 0 12 12" aria-hidden="true"><path d="M1 3.5C1 2 2.5 1 6 1s5 1 5 2.5V5H8.5V3.8h-5V5H1z M2.5 6h7l1 5h-9z"/></svg>
        044-123 456 789
      </li>
      <li class="contact__item">
        <svg class="contact__icon" viewBox="0 0 12 12" aria-hidden="true"><path d="M3 0h6v12H3z M4 1.5v8h4v-8z"/></svg>
        044-123 456 789
      </li>
      <li class="contact__item">
        <svg class="contact__icon" viewBox="0 0 12 12" aria-hidden="true"><path d="M0 2h12v8H0z M1 3l5 4 5-4z" fill-rule="evenodd"/></svg>
        info@harborledger.example
      </li>
      <li class="contact__item">
        <svg class="contact__icon" viewBox="0 0 12 12" aria-hidden="true"><circle cx="6" cy="6" r="5.5"/></svg>
        www.harborledger.example
      </li>
    </ul>
    <p class="address">12345, Address Goes Here Country Name, 123456.</p>
  </section>

</main>
</body>
</html>
```